Exclusive Crestline Groomers Invite that connects barbers

I am looking for a general invitation to join a secret club of people that shave their head. I want it the size of a business card that I can hand out to people I see on the street. I want it to feel like a special exclulisve invite to a club that only they can be apart of and want to tell their friends about.

Target Market(s)

35-60 male

Industry/Entity Type

Hair

Contact Information for Business Card

I want it to look like an invite to a secret club that only people that shave their head can be apart of... I will hand it out to people that I think fir our demographic.

Font styles to use
Serif

Colors

Designer to choose colors to be used in the design.

Requirements
Must have
• A feel of exclusivity
• website address (www.crestlinegroomers.example)
• logo

```html
<!DOCTYPE html>
<html lang="en">
<head>
<meta charset="utf-8">
<title>Crestline Groomers – Invitation Card</title>
<link href="https://fonts.googleapis.com/css2?family=Cormorant+Garamond:wght@500;600;700&display=swap" rel="stylesheet">
<style>
  :root {
    --backdrop: #333335;
    --card-dark: #454548;
    --card-light: #ffffff;
    --ink-dark: #2a2a2c;
    --ink-mid: #505053;
    --ink-light: #ffffff;
    --accent: #c9a574;
    --rule: #a8a8ab;
    --icon: #87878a;
    --mark-tone: #d9b48f;
  }
  html, body {
    margin: 0;
    width: 1200px;
    height: 801px;
    overflow: hidden;
    background: var(--backdrop);
    font-family: "Cormorant Garamond", serif;
  }
  .canvas { position: relative; width: 1200px; height: 801px; }
  .card {
    position: absolute;
    width: 310px;
    height: 502px;
    border-radius: 14px;
    box-shadow: 0 10px 28px rgba(0,0,0,.45);
    overflow: hidden;
  }
  .card--front {
    left: 236px; top: 146px;
    background: radial-gradient(ellipse at 50% 40%, #505054 0%, var(--card-dark) 70%);
    color: var(--ink-light);
  }
  .card--back { left: 658px; top: 150px; background: var(--card-light); color: var(--ink-dark); }

  .brand { position: absolute; left: 0; right: 0; text-align: center; }
  .brand__mark {
    display: block; margin: 0 auto;
    background: var(--mark-tone);
    border-radius: 3px;
  }
  .brand__name { display: block; font-weight: 700; white-space: nowrap; letter-spacing: .5px; }
  .card--front .brand { top: 110px; }
  .card--front .brand__mark { width: 60px; height: 62px; margin-bottom: 12px; }
  .card--front .brand__name { font-size: 29px; line-height: 32px; }
  .card--back .brand { top: 66px; }
  .card--back .brand__mark { width: 52px; height: 54px; margin-bottom: 8px; }
  .card--back .brand__name { font-size: 24px; line-height: 26px; color: var(--ink-dark); }

  .website {
    position: absolute; left: 0; right: 0; top: 446px;
    text-align: center; font-size: 15px; font-weight: 700; letter-spacing: .4px;
  }

  .person { position: absolute; left: 0; right: 0; top: 200px; text-align: center; }
  .person__name { font-size: 19px; font-weight: 700; letter-spacing: 1px; color: var(--ink-dark); }
  .person__role { font-size: 13.5px; font-weight: 600; letter-spacing: .8px; color: var(--ink-mid); margin-top: 2px; }

  .contact { position: absolute; left: 77px; font-size: 14.5px; font-weight: 600; color: var(--ink-mid); line-height: 17px; }
  .contact--direct { top: 361px; }
  .contact--place { top: 432px; }
  .contact__row { position: relative; padding-left: 20px; white-space: nowrap; }
  .contact__icon { position: absolute; left: 0; top: 3px; width: 11px; height: 11px; fill: var(--icon); }
  .divider { position: absolute; left: 32px; width: 248px; top: 417px; height: 1px; background: var(--rule); }
</style>
</head>
<body>
<main class="canvas">
  <section class="card card--front">
    <div class="brand">
      <span class="brand__mark"></span>
      <span class="brand__name">Crestline Groomers</span>
    </div>
    <div class="website">www.crestlinegroomers.example</div>
  </section>

  <section class="card card--back">
    <div class="brand">
      <span class="brand__mark"></span>
      <span class="brand__name">Crestline Groomers</span>
    </div>
    <div class="person">
      <div class="person__name">MARION HALE</div>
      <div class="person__role">MANAGING PARTNER</div>
    </div>

    <div class="contact contact--direct">
      <div class="contact__row">
        <svg class="contact__icon" viewBox="0 0 12 12"><circle cx="6" cy="6" r="6"/><path d="M4 3.2l1 1.6-.6.7c.5 1 1.2 1.7 2.1 2.1l.7-.6 1.6 1-.5 1.1C6 9 3 6 2.9 3.7z" fill="#fff"/></svg>
        O) 303.555.0142
      </div>
      <div class="contact__row">C) 303.555.0187</div>
      <div class="contact__row">
        <svg class="contact__icon" viewBox="0 0 12 12"><circle cx="6" cy="6" r="6"/><rect x="3" y="4" width="6" height="4" fill="#fff"/><path d="M3 4l3 2.2L9 4" stroke="#87878a" stroke-width=".8" fill="none"/></svg>
        mhale@crestlinegroomers.example
      </div>
    </div>

    <div class="divider"></div>

    <div class="contact contact--place">
      <div class="contact__row">
        <svg class="contact__icon" viewBox="0 0 12 14" style="height:13px"><path d="M6 0a4.5 4.5 0 0 1 4.5 4.5C10.5 8 6 12 6 12S1.5 8 1.5 4.5A4.5 4.5 0 0 1 6 0z"/><circle cx="6" cy="4.5" r="1.6" fill="#fff"/><ellipse cx="6" cy="13" rx="3.5" ry="1" fill="none" stroke="#87878a" stroke-width=".8"/></svg>
        480 Ridge Ave #120,
      </div>
      <div class="contact__row">Lakewood, CO 80214</div>
    </div>
  </section>
</main>
</body>
</html>
```